Landscaping flier 2024

Create a 1 page flier for landscaping services
1. Must be completed in Adobe Photoshop
2. Size 8.5" x 11" (portrait layout)
3. Include logo
4. Text to include:
2024 Gravesite Landscaping Packages
info@hollowbrookmemorial.org
(201) 555-0148
hollowbrookmemorial.org
5. Use chart text for the content. DO NOT COPY THE CHART DESIGN/FORMAT. Use the chart for the text you need only.
6. Use "Pricing cards as format for laying out the chart". Open to other ideas as well.
**Use the example of chart design (handwritten) to base your design off of.
7. Photos
-include before and after care photos

```html
<!DOCTYPE html>
<html lang="en">
<head>
<meta charset="utf-8">
<title>2024 Gravesite Landscaping Packages – Hollowbrook Memorial</title>
<link rel="stylesheet" href="https://fonts.googleapis.com/css2?family=Libre+Baskerville:wght@700&family=Montserrat:wght@400;600;700;800&display=swap">
<style>
:root{
  --page:#e9e9e7;
  --paper:#ffffff;
  --burgundy:#8c2436;
  --burgundy-dark:#6e1a2a;
  --navy:#223246;
  --navy-dark:#18253a;
  --sky:#2ba6dc;
  --sky-dark:#1b8cc4;
  --gold:#d9b54a;
  --tick:#6cc04a;
  --cross:#e0413f;
  --ink:#3a3f47;
  --muted:#6b7078;
}
*{box-sizing:border-box;margin:0;padding:0}
html,body{width:1200px;height:2415px;overflow:hidden;background:var(--page)}
body{position:relative;font-family:"Montserrat",Arial,sans-serif;color:var(--ink)}
.flyer{position:absolute;left:90px;top:527px;width:1020px;height:1360px;background:var(--paper);box-shadow:0 10px 30px rgba(0,0,0,.15);overflow:hidden}
.title{position:absolute;left:0;width:100%;text-align:center;font-family:"Libre Baskerville",Georgia,serif;font-weight:700;color:var(--burgundy);letter-spacing:.5px}
.title-top{top:44px;font-size:38px}
.title-bottom{top:100px;font-size:40px}
.hero-photo{position:absolute;left:0;top:160px;width:100%;height:300px;background:linear-gradient(180deg,#fff 0%,#dfe4d4 12%,#b9b65a 30%,#8d9a52 50%,#5e7a3c 72%,#3f5a2c 100%)}
.hero-bands{position:absolute;left:0;top:410px}
.card{position:absolute;color:#fff;text-align:center}
.card-seasonal{left:36px;top:450px;width:295px;height:587px;background:linear-gradient(180deg,var(--sky) 0%,var(--sky-dark) 100%)}
.card-basic{left:341px;top:450px;width:324px;height:599px;background:linear-gradient(180deg,#2b4160 0%,var(--navy) 30%,var(--navy-dark) 100%)}
.card-perpetual{left:672px;top:416px;width:317px;height:645px;background:linear-gradient(180deg,#a12d45 0%,var(--burgundy) 40%,var(--burgundy-dark) 100%)}
.card-header{padding:26px 14px 0}
.card-title{font-weight:800;font-size:23px;line-height:1.05;text-transform:uppercase}
.card-sub{margin-top:6px;font-size:10.5px;line-height:1.3;text-transform:uppercase;opacity:.85}
.card-divider{margin:12px auto 0;width:80%;height:1px;background:rgba(255,255,255,.45);position:relative}
.card-divider::after{content:"";position:absolute;left:50%;top:-5px;width:10px;height:10px;margin-left:-5px;border-radius:50%;background:#fff}
.price-row{display:flex;align-items:center;justify-content:center;gap:10px;margin-top:30px}
.price-label{font-size:12px;font-weight:600;line-height:1.2;text-align:right;text-transform:uppercase}
.price-amount{font-size:50px;font-weight:700;line-height:1}
.price-amount sup{font-size:22px;vertical-align:top;position:relative;top:4px}
.price-note{margin-top:12px;font-size:12px;opacity:.85}
.tiers{display:flex;align-items:flex-start;gap:8px;padding:26px 16px 0 22px}
.tier{width:44px;text-align:center}
.tier-bubble{width:44px;height:54px;border-radius:22px 22px 22px 22px;background:#1672a7;display:flex;flex-direction:column;align-items:center;justify-content:center;font-weight:700;font-size:22px;line-height:1}
.tier-bubble small{font-size:7px;font-weight:600;text-transform:uppercase;margin-top:2px}
.tier-price{margin-top:6px;font-size:11px;font-weight:700}
.tier-note{margin-left:8px;text-align:left;font-size:11px;line-height:1.25;padding-top:8px}
.weeding{display:flex;align-items:center;gap:10px;margin:24px 12px 0;padding:10px 10px;background:rgba(0,0,0,.14);text-align:left}
.weeding-label{font-size:9.5px;font-weight:800;text-transform:uppercase;line-height:1.2;white-space:nowrap}
.weeding-text{font-size:10px;line-height:1.3}
.features{list-style:none;text-align:left;padding:20px 0 0 36px}
.features li{position:relative;font-size:14px;line-height:1.25;margin-bottom:15px;padding-left:22px}
.features li::before{content:"";position:absolute;left:0;top:2px;width:14px;height:14px;border-radius:50%;border:2px solid #fff}
.features li.yes::before{background:var(--tick)}
.features li.no::before{background:var(--cross)}
.ribbon{position:absolute;left:-26px;top:14px;width:120px;transform:rotate(-35deg);background:var(--gold);color:var(--burgundy-dark);font-size:8.5px;font-weight:800;text-transform:uppercase;text-align:center;padding:4px 0}
.footer-brand{position:absolute;left:62px;top:1138px;display:flex;align-items:center;gap:14px}
.brand-dot{width:40px;height:40px;border-radius:50%;background:#d8d9dc}
.brand-name{font-family:"Libre Baskerville",Georgia,serif;font-weight:700;font-size:30px;color:var(--burgundy)}
.contact{position:absolute;left:118px;list-style:none}
.contact li{display:flex;align-items:center;gap:14px;font-size:17px;color:var(--ink);margin-bottom:20px}
.contact li.phone{font-weight:700;font-size:20px}
.contact svg{width:18px;height:18px;flex:none}
.contact-list{top:1212px}
.care-photo{position:absolute;top:1150px;width:196px;height:190px;background:linear-gradient(180deg,#c6cfc2 0%,#7aa35a 35%,#5f9a3a 70%,#4b7e2e 100%)}
.care-before{left:569px}
.care-after{left:785px}
.care-tag{position:absolute;top:-12px;left:50%;transform:translateX(-50%);background:var(--burgundy);color:#fff;font-size:12px;font-weight:600;font-style:italic;padding:4px 14px;white-space:nowrap}
</style>
</head>
<body>
<main class="flyer">
  <h1 class="title title-top">2024 GRAVESITE</h1>
  <h2 class="title title-bottom">LANDSCAPING PACKAGES</h2>

  <div class="hero-photo" role="img" aria-label="Photo of the memorial grounds with headstones, autumn trees and the historic main building"></div>
  <svg class="hero-bands" width="1020" height="60" viewBox="0 0 1020 60">
    <polygon points="0,18 120,40 0,60" fill="var(--burgundy)"/>
    <polygon points="900,40 1020,0 1020,60" fill="var(--navy)"/>
  </svg>

  <section class="card card-seasonal">
    <div class="card-header">
      <div class="card-title">Seasonal Care</div>
      <div class="card-sub">Seasonal landscaping<br>grave care</div>
      <div class="card-divider"></div>
    </div>
    <div class="tiers">
      <div class="tier"><div class="tier-bubble">1<small>year</small></div><div class="tier-price">$132</div></div>
      <div class="tier"><div class="tier-bubble">3<small>years</small></div><div class="tier-price">$396</div></div>
      <div class="tier"><div class="tier-bubble">2<small>years</small></div><div class="tier-price">$264</div></div>
      <div class="tier-note">Multi-year payment locks in current rates</div>
    </div>
    <div class="weeding">
      <div class="weeding-label">Weeding &amp;<br>Trimming<br>on your<br>gravesite</div>
      <div class="weeding-text">Approximately Every 7 Weeks During The Growing Season Mid-April Through Mid-October</div>
    </div>
    <ul class="features">
      <li class="no">Payment Ensures<br>Grave Care Forever</li>
      <li class="no">Monument Leveling</li>
      <li class="no">Monument Cleaning</li>
      <li class="no">Full Bed Of Boxwood Shrubs</li>
      <li class="no">Replacement Of Shrubs</li>
      <li class="no">Trust Certificate</li>
    </ul>
  </section>

  <section class="card card-basic">
    <div class="card-header">
      <div class="card-title">Basic Care<br>Endowment</div>
      <div class="card-sub">Landscaping care forever<br>for graves with no plantings</div>
      <div class="card-divider"></div>
    </div>
    <div class="price-row">
      <div class="price-label">12 Monthly<br>payments of</div>
      <div class="price-amount"><sup>$</sup>287</div>
    </div>
    <div class="price-note">Call for single payment discount</div>
    <div class="weeding">
      <div class="weeding-label">Weeding &amp;<br>Trimming on<br>your gravesite</div>
      <div class="weeding-text">2 times per year:<br>mid-May &amp; mid-September</div>
    </div>
    <ul class="features">
      <li class="yes">Payment Ensures<br>Grave Care Forever</li>
      <li class="yes">Monument Leveling</li>
      <li class="no">Monument Cleaning</li>
      <li class="no">Full Bed Of Boxwood Shrubs</li>
      <li class="no">Replacement Of Shrubs</li>
      <li class="no">Trust Certificate</li>
    </ul>
  </section>

  <section class="card card-perpetual">
    <div class="ribbon">Most popular</div>
    <div class="card-header">
      <div class="card-title">Perpetual Care<br>Endowment</div>
      <div class="card-sub">Landscaping care forever<br>for graves with plantings</div>
      <div class="card-divider"></div>
    </div>
    <div class="price-row">
      <div class="price-label">12 Monthly<br>payments of</div>
      <div class="price-amount"><sup>$</sup>351</div>
    </div>
    <div class="price-note">Call for single payment discount</div>
    <div class="weeding">
      <div class="weeding-label">Weeding &amp;<br>Trimming on<br>your gravesite</div>
      <div class="weeding-text">Approximately every 7 weeks during the growing season, mid-April through mid-October</div>
    </div>
    <ul class="features">
      <li class="yes">Payment Ensures<br>Grave Care Forever</li>
      <li class="yes">Monument Leveling</li>
      <li class="yes">Monument Cleaning</li>
      <li class="yes">Full Bed Of Boxwood Shrubs</li>
      <li class="yes">Replacement Of Shrubs</li>
      <li class="yes">Trust Certificate</li>
    </ul>
  </section>

  <div class="footer-brand">
    <span class="brand-dot"></span>
    <span class="brand-name">Hollowbrook Memorial</span>
  </div>

  <ul class="contact contact-list">
    <li class="phone">
      <svg viewBox="0 0 24 24"><path d="M6.6 10.8a15 15 0 0 0 6.6 6.6l2.2-2.2a1 1 0 0 1 1-.25 11.4 11.4 0 0 0 3.6.57 1 1 0 0 1 1 1V20a1 1 0 0 1-1 1A17 17 0 0 1 3 4a1 1 0 0 1 1-1h3.5a1 1 0 0 1 1 1c0 1.25.2 2.45.57 3.57a1 1 0 0 1-.25 1z" fill="var(--burgundy)"/></svg>
      (201) 555-0148
    </li>
    <li>
      <svg viewBox="0 0 24 24"><rect x="2" y="5" width="20" height="14" rx="2" fill="none" stroke="var(--burgundy)" stroke-width="2"/><path d="M3 6l9 7 9-7" fill="none" stroke="var(--burgundy)" stroke-width="2"/></svg>
      info@hollowbrookmemorial.org
    </li>
    <li>
      <svg viewBox="0 0 24 24"><circle cx="12" cy="12" r="9.5" fill="none" stroke="var(--burgundy)" stroke-width="2"/><path d="M2.5 12h19M12 2.5c3 3 3 16 0 19M12 2.5c-3 3-3 16 0 19" fill="none" stroke="var(--burgundy)" stroke-width="1.6"/></svg>
      www.hollowbrookmemorial.org
    </li>
  </ul>

  <div class="care-photo care-before" role="img" aria-label="Before care photo: overgrown gravesite with untrimmed shrubs">
    <span class="care-tag">Before Care</span>
  </div>
  <div class="care-photo care-after" role="img" aria-label="After care photo: neatly trimmed boxwood bed and cleaned monument">
    <span class="care-tag">After care</span>
  </div>
</main>
</body>
</html>
```